Core Value Graphic for a Service Disabled and Minority Certified contractor

My company, Keystone Aid Partners, is a US Federal Contractor that hires veterans and service disabled veterans. Our website is www.keystoneaid7.example. We work hard to maintain a 50:50 split between veterans and non-veterans on our team. Our tagline is "To Find a Better Way." We are continually looking to integrate technology and efficiency into all that we do.

I want a way to express our company core values visually so that our employees and customers alike can read them and get a sense of who we are, what drives us to succeed, and what makes up our team DNA.

I need an artist like you to help me represent our core values visually. In a manner that I can print it out on an 8"X11" sheet of paper or a large 48" X 48" poster, without losing the visual clarity or that it pixelates out of focus. I am looking for a color scheme that is patriotic with Red, White, and Blues and similar hues. I would also like to incorporate my logo and tagline into the design in some manner.

I have attached several examples of a Core Value Grids from other companies. I am hopeful it will inspire you, and a get your brain juices flowing to provide me with a knockout Core Value Grid that will rock only you can provide! I also include a copy of my company Core Values and a copy of our Logo.

Looking forward to seeing your creations. Thanks.

Target Market(s)

Employees, any potential strategic alliance partners, and customers.

Industry/Entity Type

Contractor

Requirements
Must have
• Patriotic feel and have my logo someplace on the document.

```html
<!DOCTYPE html>
<html lang="en">
<head>
<meta charset="utf-8">
<title>Keystone Aid Partners – Core Values</title>
<link rel="stylesheet" href="https://fonts.googleapis.com/css2?family=Exo+2:wght@500;600&family=Roboto:wght@400&family=Montserrat:wght@700&display=swap">
<style>
  :root{
    --backdrop:#cfcfcf;
    --navy:#152f52;
    --red:#ab0f16;
    --oval:#972520;
    --label:#a8201c;
    --ink:#3a3a3a;
    --card-top:#ffffff;
    --card-bottom:#dedede;
    --green:#2e9a3e;
    --purple:#8a1f6e;
    --teal:#3e8f7f;
    --magenta:#d4177a;
  }
  *{box-sizing:border-box;margin:0;padding:0}
  html,body{width:1200px;height:771px;overflow:hidden;background:var(--backdrop)}
  body{position:relative;font-family:"Roboto",Arial,sans-serif;color:var(--ink)}
  .board{position:absolute;left:189px;top:94px;width:822px;height:582px;background:var(--navy)}
  .band{position:absolute;left:189px;top:136px;width:822px;height:32px;background:var(--red)}
  .brand{position:absolute;left:531px;top:124px;width:137px;height:58px;background:#fff;
    display:flex;align-items:center;justify-content:center;gap:6px;padding:0 8px}
  .brand-mark{width:12px;height:12px;background:var(--red);flex:none}
  .brand-name{font-family:"Exo 2",Arial,sans-serif;font-weight:600;font-size:13px;line-height:14px;color:var(--navy)}
  .card{position:absolute;background:linear-gradient(180deg,var(--card-top) 30%,var(--card-bottom));}
  .card p{font-size:7.2px;line-height:10.3px;margin-bottom:3px}
  .card .lbl{color:var(--label)}
  .title{font-family:"Exo 2",Arial,sans-serif;font-weight:500;color:var(--navy);font-size:17.5px;line-height:20px}
  .icon{position:absolute;border-radius:50%}
  .top .title{font-size:16px;white-space:nowrap}
  .oval-gap{width:80px;height:150px}
  .safety{left:220px;top:203px;width:376px;height:189px}
  .safety .icon{left:12px;top:23px;width:32px;height:32px;background:radial-gradient(circle,var(--green) 45%,#fff 47%,#fff 58%,var(--green) 60%)}
  .safety .title{position:absolute;left:55px;top:29px}
  .safety .body{position:absolute;left:35px;top:62px;width:275px;text-align:justify}
  .safety .oval-gap{float:right;shape-outside:ellipse(126px 78px at 150px 93px)}
  .innovate{left:604px;top:203px;width:375px;height:189px}
  .innovate .icon{left:11px;top:27px;width:66px;height:30px;border-radius:15px;background:linear-gradient(90deg,var(--navy) 0 30%,var(--red) 30% 70%,var(--navy) 70%)}
  .innovate .title{position:absolute;left:98px;top:29px}
  .innovate .body{position:absolute;right:14px;top:62px;width:305px;text-align:right}
  .innovate .oval-gap{float:left;shape-outside:ellipse(126px 78px at -60px 93px)}
  .bottom .icon{left:50%;transform:translateX(-50%);top:16px;width:36px;height:36px}
  .bottom .title{text-align:center;position:absolute;left:0;right:0}
  .bottom .body{position:absolute;left:18px;right:18px;text-align:justify}
  .wingman{left:220px;top:400px;width:249px;height:242px}
  .wingman .icon{background:linear-gradient(180deg,#444 0 45%,var(--purple) 45%)}
  .wingman .title{top:70px}
  .wingman .body{top:103px}
  .troops{left:477px;top:400px;width:245px;height:242px}
  .troops .icon{z-index:3;top:24px;width:68px;height:36px;border-radius:8px;background:linear-gradient(90deg,var(--teal) 0 30%,#6a5aa8 30% 70%,var(--teal) 70%)}
  .troops .title{top:75px}
  .troops .body{top:123px}
  .fail{left:730px;top:400px;width:249px;height:242px}
  .fail .icon{top:20px;width:54px;height:40px;border-radius:4px;background:linear-gradient(90deg,var(--magenta) 48%,var(--green) 48% 52%,var(--magenta) 52%)}
  .fail .title{top:78px}
  .fail .body{top:116px}
  .tagline{position:absolute;left:480px;top:286px;width:240px;height:144px;border-radius:50%;background:var(--oval);z-index:2;
    display:flex;align-items:center;justify-content:center;text-align:center;
    font-family:"Montserrat",Arial,sans-serif;font-weight:700;font-size:29px;line-height:33px;letter-spacing:1.5px;color:#fff}
</style>
</head>
<body>
  <div class="board"></div>
  <div class="band"></div>
  <div class="brand"><span class="brand-mark"></span><span class="brand-name">Keystone Aid Partners</span></div>

  <section class="card top safety">
    <div class="icon" role="img" aria-label="Tree inside circling arrows icon"></div>
    <h2 class="title">Everyone comes back to the Green Zone.</h2>
    <div class="body">
      <div class="oval-gap"></div>
      <p><span class="lbl">WHAT IT MEANS - </span> Safety takes precedence over every phase of the day's operation.</p>
      <p><span class="lbl">HOW TO EXPRESS IT - </span>Anyone can call a stop to the work in progress if an unsafe act is occurring. In fact, it is each team member's duty to do so, rectify the unsafe issue, then proceed. Never hesitate; everyone comes back. Finally, each After Action Review begins with discussing safety issues. We always let everyone on the team know of an unsafe situation, so it can be avoided in the future.</p>
      <p><span class="lbl">RESULT - </span>All team members go home to their loved ones each day to pursue their individual happiness.</p>
    </div>
  </section>

  <section class="card top innovate">
    <div class="icon" role="img" aria-label="Binoculars icon"></div>
    <h2 class="title">Boldly go. Seek. Find.</h2>
    <div class="body">
      <div class="oval-gap"></div>
      <p><span class="lbl">WHAT IT MEANS: - </span> We weave innovation into the fabric that makes up our company.</p>
      <p><span class="lbl">HOW TO EXPRESS IT: - </span>We're early adopters of technology. We quickly evaluate new technologies or processes that could separate us from our competition. Then we implement and evaluate these new technologies. We dump it quickly if we see it is not helping us achieve "Commander's Intent." We have the guts to be first. We iterate continuously and attack, attack, attack.</p>
      <p><span class="lbl">RESULT: - </span> We will be ahead of our competition. It' one mechanism that helps us scale. Prosperity favors the bold!</p>
    </div>
  </section>

  <div class="tagline">TO FIND<br>A BETTER<br>WAY</div>

  <section class="card bottom wingman">
    <div class="icon" role="img" aria-label="Person figure icon"></div>
    <h2 class="title">Never leave your wingman</h2>
    <div class="body">
      <p><span class="lbl">WHAT IT MEANS – </span> We always help your team members be successful. Commitment to each other and to our own personal integrity is the fuel that empowers us.</p>
      <p><span class="lbl">HOW TO EXPRESS IT – </span> If a Wingman is having challenges accomplishing their individual priorities or completing their assigned mission, volunteer to help them to do so.</p>
      <p>This goes for Subs/Suppliers as well. We help those who help us succeed! Always look to establish the best win-win relationship possible, and do what you can to support them if they get into a bind.</p>
      <p><span class="lbl">RESULT – </span>Be there for them and they will be there for us.</p>
    </div>
  </section>

  <section class="card bottom troops">
    <div class="icon" role="img" aria-label="Group of team members icon"></div>
    <h2 class="title">Troops (Team Members)<br>eat first</h2>
    <div class="body">
      <p><span class="lbl">WHAT IT MEANS – </span>No leader will put themselves ahead of their subordinates.</p>
      <p><span class="lbl">HOW TO EXPRESS IT – </span> We lead by example. Demonstrate the moral courage and discipline to do the right thing at the highest level of quality.</p>
      <p><span class="lbl">RESULT – </span> Every new teammember's will quickly realize their leaders genuinely care for their welfare and success.</p>
      <p>This is the best way to drive Esprit de Corps and achieve excellence.</p>
    </div>
  </section>

  <section class="card bottom fail">
    <div class="icon" role="img" aria-label="Open book icon"></div>
    <h2 class="title">Fail quickly and learn</h2>
    <div class="body">
      <p><span class="lbl">WHAT IT MEANS – </span> If you're not making mistakes, you're not taking enough chances or getting out of your comfort zone.</p>
      <p><span class="lbl">HOW TO EXPRESS IT – </span> Use your best judgment when trying something new. But, don't let your pride keep you from saying, "I was wrong" when your idea doesn't work. We trust you will know when it's time to dump the idea, or stop doing something that doesn't work.</p>
      <p><span class="lbl">RESULT – </span> No one will ever be penalized for making a mistake. Don't be afraid to try something you believe will work. That's how we grow ourselves and our team members.</p>
    </div>
  </section>
</body>
</html>
```